Renewed Website Design for B2B Company

We need a renewed design for Van Roost - an international trading company in raw materials: natural oils (essential oils, fatty oils, and extracts) and related products such as aromas, fragrances, etc.

Page designs to create:

1. Home page (see the mockup, the content and structure should be exactly like this, however feel free creative-wise)

2. Products page(includes all the 11 product categories which you see on van-roost.nl and some small description of them).

Current website: van-roost.nl
Competitors' websites: brivelmaroilworks.com & qtuvx.com (they don't have particularly perfect websites design-wise, however, it's mostly to give you the idea of this market).

Please, go to this Google Drive folder - https://kortlink.example/7TxwPq - to see Van Roost's logo in different variations, brandbook with colors, fonts, and a brochure with 'mood board' pictures.

Target Market(s)

B2B companies needing white label products like natural/essential/fatty oils, fragrances etc.

Number of Pages Required

2 page

Font styles to use
Other font styles liked:
• Open Sans

Colors

Designer to choose colors to be used in the design.

Requirements
Should not have
• No images with people; no turqoise, blue or pink colors; no overlays over pictures

```html
<!DOCTYPE html>
<html lang="nl">
<head>
<meta charset="utf-8">
<title>Van Roost – Home</title>
<link href="https://fonts.googleapis.com/css2?family=Open+Sans:wght@400;600;700&family=Ubuntu:wght@400;500;700&display=swap" rel="stylesheet">
<style>
:root{
  --green:#034420;
  --green-text:#0a4a23;
  --green-soft:#3f7a55;
  --red:#c8102e;
  --hero-bg:#e6ecea;
  --ink:#2b2b2b;
  --line:#6e8f7a;
  --white:#ffffff;
}
*{margin:0;padding:0;box-sizing:border-box}
html,body{width:1200px;height:4142px;overflow:hidden;background:var(--white)}
body{position:relative;font-family:'Open Sans',sans-serif;color:var(--ink)}
.abs{position:absolute}
.heading{font-family:'Ubuntu',sans-serif;font-weight:500;color:var(--green-text)}
.brand{display:flex;align-items:center;gap:12px}
.brand-dot{width:42px;height:42px;border-radius:50%;background:var(--green)}
.brand-name{font-family:'Ubuntu',sans-serif;font-weight:700;font-size:38px;color:var(--red);letter-spacing:.5px}
.nav{display:flex;font-size:17px;color:#333}
.nav a{color:inherit;text-decoration:none}
.btn{display:inline-flex;align-items:center;justify-content:center;background:var(--red);color:var(--white);font-family:'Ubuntu',sans-serif;font-weight:500;font-size:17px;text-decoration:none;border-radius:28px 28px 28px 4px}
.body-text{font-size:17px;line-height:30px;color:#333}
.rule{height:1px;background:var(--line)}
.photo{display:block}
</style>
</head>
<body>

<!-- Header -->
<header>
  <div class="abs brand" style="left:110px;top:24px">
    <span class="brand-dot"></span><span class="brand-name">VAN ROOST</span>
  </div>
  <nav class="abs nav" style="left:550px;top:34px">
    <a href="#" style="font-weight:700;color:var(--green-text)">Huis</a>
    <a href="#" style="margin-left:50px">Over ons</a>
    <a href="#" style="margin-left:50px">Producten</a>
    <a href="#" style="margin-left:50px">Contact</a>
  </nav>
  <svg class="abs" style="left:1000px;top:30px" width="30" height="30" viewBox="0 0 30 30" aria-label="Zoeken">
    <circle cx="15" cy="15" r="15" fill="var(--green)"/>
    <circle cx="14" cy="14" r="5" fill="none" stroke="#fff" stroke-width="2"/>
    <line x1="18" y1="18" x2="21" y2="21" stroke="#fff" stroke-width="2"/>
  </svg>
  <svg class="abs" style="left:1058px;top:30px" width="30" height="30" viewBox="0 0 30 30" aria-label="Nederlands">
    <clipPath id="flagclip"><circle cx="15" cy="15" r="15"/></clipPath>
    <g clip-path="url(#flagclip)"><rect width="30" height="10" fill="#c8102e"/><rect y="10" width="30" height="10" fill="#fff"/><rect y="20" width="30" height="10" fill="#21468b"/></g>
  </svg>
</header>

<!-- Hero -->
<section>
  <svg class="abs" style="left:0;top:80px" width="1200" height="680" viewBox="0 0 1200 680">
    <path d="M0 0H1200V590Q600 700 0 600Z" fill="var(--hero-bg)"/>
    <path d="M250 632Q600 680 940 632Q600 668 250 632Z" fill="var(--green)"/>
  </svg>
  <svg class="abs" style="left:640px;top:190px" width="425" height="475" viewBox="0 0 100 115" aria-hidden="true">
    <path d="M50 0C65 20 100 45 100 65A50 50 0 0 1 0 65C0 45 35 20 50 0Z" fill="#d3ddd8" opacity=".7"/>
  </svg>
  <div class="abs photo" role="img" aria-label="Amber essential oil bottles with orange blossom and green leaves" style="left:16px;top:140px;width:530px;height:540px;border-radius:40% 40% 20% 20%;background:radial-gradient(ellipse at 55% 45%,#8a4a18 0%,#b9722e 22%,#5d9a3a 45%,rgba(230,236,234,0) 72%)"></div>
  <h1 class="abs heading" style="left:600px;top:284px;width:510px;text-align:center;font-size:74px;line-height:82px">Welkom bij<br>Van Roost</h1>
  <a class="abs btn" href="#" style="left:787px;top:476px;width:131px;height:55px">Leer Meer</a>
</section>

<!-- Intro -->
<p class="abs" style="left:120px;top:820px;width:960px;text-align:center;font-family:'Ubuntu',sans-serif;font-size:26px;line-height:41px;color:#222">
  <span style="color:var(--red);font-weight:500">Van Roost</span> is een solide en betrouwbare leverancier van grondstoffen voor de <strong style="font-weight:500">cosmetische-, chemische, reform-, feed- en foodsector</strong>. Wij onderscheiden ons door een hoog serviceniveau en uitgebreid aanbod.
</p>

<svg width="0" height="0" style="position:absolute">
  <defs>
    <filter id="dropShadow" x="-20%" y="-20%" width="140%" height="140%"><feDropShadow dx="0" dy="4" stdDeviation="4" flood-opacity=".3"/></filter>
    <linearGradient id="gOil" x1="0" y1="0" x2="1" y2="1"><stop offset="0" stop-color="#c9c7c0"/><stop offset=".45" stop-color="#e98a2c"/><stop offset="1" stop-color="#8d6a3d"/></linearGradient>
    <linearGradient id="gParfum" x1="0" y1="0" x2="1" y2="1"><stop offset="0" stop-color="#f1f0ee"/><stop offset=".5" stop-color="#d99aa0"/><stop offset="1" stop-color="#b08356"/></linearGradient>
    <linearGradient id="gRaw" x1="0" y1="0" x2="1" y2="1"><stop offset="0" stop-color="#f3c3cb"/><stop offset=".55" stop-color="#e8a7b6"/><stop offset="1" stop-color="#8a7aa0"/></linearGradient>
  </defs>
</svg>

<!-- Natuurlijk oliën -->
<section>
  <h2 class="abs heading" style="left:110px;top:1110px;font-size:36px">Natuurlijk oliën</h2>
  <div class="abs rule" style="left:110px;top:1166px;width:690px"></div>
  <p class="abs body-text" style="left:111px;top:1180px;width:540px">Keuze uit een uitgebreid assortiment uit voorraad leverbare etherische en vette oliën. Niet op voorraad? Geen probleem! Door onze ruime ervaring en wereldwijde netwerk is nauwelijks een natuurlijke olie die wij niet kunnen leveren.</p>
  <svg class="abs" style="left:777px;top:1026px" width="317" height="365" viewBox="0 0 100 115" role="img" aria-label="Pipette dripping oil into a glass bottle beside sliced oranges">
    <path d="M50 0C65 20 100 45 100 65A50 50 0 0 1 0 65C0 45 35 20 50 0Z" fill="url(#gOil)" filter="url(#dropShadow)"/>
  </svg>
</section>

<!-- Parfums en Aroma's -->
<section>
  <svg class="abs" style="left:110px;top:1404px" width="316" height="365" viewBox="0 0 100 115" role="img" aria-label="Dropper bottles with rose petals and perfume vials">
    <path d="M50 0C65 20 100 45 100 65A50 50 0 0 1 0 65C0 45 35 20 50 0Z" fill="url(#gParfum)" filter="url(#dropShadow)"/>
  </svg>
  <h2 class="abs heading" style="right:111px;top:1488px;font-size:36px">Parfums en Aroma’s</h2>
  <div class="abs rule" style="left:407px;top:1541px;width:682px"></div>
  <p class="abs body-text" style="right:111px;top:1557px;width:520px;text-align:right">Geur- en smaakstoffen onder de merknaam Aromvia. Onze specialisten ontwikkelen eigen parfum compounds en flavour compounds voor elke toepassing. De mogelijkheden zijn eindeloos.</p>
</section>

<!-- Grondstoffen -->
<section>
  <h2 class="abs heading" style="left:110px;top:1871px;font-size:36px">Grondstoffen</h2>
  <div class="abs rule" style="left:110px;top:1927px;width:690px"></div>
  <p class="abs body-text" style="left:111px;top:1941px;width:540px">Ingrediënten en halffabricaten die afgeleid zijn van of veel gebruikt worden met natuurlijke oliën. Voor veel producerende bedrijven zijn wij daarmee een one-stop-shop partner.</p>
  <svg class="abs" style="left:777px;top:1773px" width="316" height="365" viewBox="0 0 100 115" role="img" aria-label="Bowl of dried lavender with small glass bottles">
    <path d="M50 0C65 20 100 45 100 65A50 50 0 0 1 0 65C0 45 35 20 50 0Z" fill="url(#gRaw)" filter="url(#dropShadow)"/>
  </svg>
</section>

<!-- Over ons -->
<section class="abs" style="left:0;top:2252px;width:1200px;height:421px;background:var(--green)">
  <div class="abs photo" role="img" aria-label="Amber dropper bottles on a white plate" style="left:111px;top:37px;width:224px;height:282px;border-radius:100px 100px 0 100px;background:linear-gradient(160deg,#f2f2ef 0%,#e4e2dc 40%,#8a4b1d 70%,#d7d5cf 100%)"></div>
  <div class="abs photo" role="img" aria-label="Small amber dropper bottle held up" style="left:347px;top:193px;width:152px;height:193px;border-radius:0 76px 0 76px;background:linear-gradient(170deg,#f1efeb 0%,#e8e3dc 50%,#9a5a2a 75%,#efe7de 100%)"></div>
  <h2 class="abs heading" style="right:111px;top:98px;font-size:36px;color:var(--white)">Over ons</h2>
  <div class="abs" style="left:563px;top:161px;width:526px;height:1px;background:#6c9a7d"></div>
  <p class="abs body-text" style="right:111px;top:186px;width:530px;text-align:right;color:var(--white)">Dit zijn wij, een groeiend familiebedrijf in Hoorndal (Verlo) dat werkt met een professioneel en hecht team &lt;link en beeld&gt;. Wij vinden het van groot belang dat onze klanten tevreden zijn, daarom proberen wij altijd net dat stapje extra te zetten.</p>
</section>

<!-- Story CTA -->
<section>
  <div class="abs photo" role="img" aria-label="Herbs, lavender and oil jars laid out on a wooden surface" style="left:0;top:2880px;width:1200px;height:241px;background:linear-gradient(180deg,rgba(255,255,255,1) 0%,rgba(214,220,206,.8) 35%,#8e9c6e 70%,#6f7d4f 100%)"></div>
  <p class="abs" style="left:150px;top:2754px;width:900px;text-align:center;font-family:'Ubuntu',sans-serif;font-size:26px;line-height:41px;color:var(--green-text)">Van Roost (anno 1979) has been around for more than 40 years. Would you like to know more about the story behind Van Roost?</p>
  <a class="abs btn" href="#" style="left:534px;top:2879px;width:132px;height:55px">Leer Meer</a>
</section>

<!-- Werkwijze -->
<section class="abs" style="left:0;top:3121px;width:1200px;height:700px;background:var(--green)">
  <h2 class="abs heading" style="left:0;top:67px;width:1200px;text-align:center;font-size:36px;color:var(--white)">Werkwijze</h2>
  <div class="abs" style="left:339px;top:133px;width:522px;height:1px;background:#6c9a7d"></div>

  <svg class="abs" style="left:109px;top:197px" width="180" height="185" viewBox="0 0 104 115" role="img" aria-label="Wooden box filled with small oil bottles">
    <path d="M54 0C69 20 104 45 104 65A50 50 0 0 1 4 65C4 45 39 20 54 0Z" fill="var(--green-soft)"/>
    <path d="M50 0C65 20 100 45 100 65A50 50 0 0 1 0 65C0 45 35 20 50 0Z" fill="#c79a6a" stroke="#fff" stroke-width="1.5"/>
  </svg>
  <svg class="abs" style="left:386px;top:197px" width="180" height="185" viewBox="0 0 104 115" role="img" aria-label="Hand holding a small dropper bottle">
    <path d="M54 0C69 20 104 45 104 65A50 50 0 0 1 4 65C4 45 39 20 54 0Z" fill="var(--green-soft)"/>
    <path d="M50 0C65 20 100 45 100 65A50 50 0 0 1 0 65C0 45 35 20 50 0Z" fill="#e6cdbd" stroke="#fff" stroke-width="1.5"/>
  </svg>
  <svg class="abs" style="left:648px;top:197px" width="180" height="185" viewBox="0 0 104 115" role="img" aria-label="Crate with bottles and green herbs">
    <path d="M54 0C69 20 104 45 104 65A50 50 0 0 1 4 65C4 45 39 20 54 0Z" fill="var(--green-soft)"/>
    <path d="M50 0C65 20 100 45 100 65A50 50 0 0 1 0 65C0 45 35 20 50 0Z" fill="#a98e66" stroke="#fff" stroke-width="1.5"/>
  </svg>
  <svg class="abs" style="left:910px;top:197px" width="180" height="185" viewBox="0 0 104 115" role="img" aria-label="Tray with amber bottles and flowers">
    <path d="M54 0C69 20 104 45 104 65A50 50 0 0 1 4 65C4 45 39 20 54 0Z" fill="var(--green-soft)"/>
    <path d="M50 0C65 20 100 45 100 65A50 50 0 0 1 0 65C0 45 35 20 50 0Z" fill="#c98a4a" stroke="#fff" stroke-width="1.5"/>
  </svg>

  <p class="abs" style="left:111px;top:409px;width:225px;font-size:16px;line-height:28px;color:var(--white)">Wij leveren grondstoffen uit voorraad , standaard verpakt in IBC’s, vaten of jerrycans, maar ook levering in kleinere verpakkingen zijn bij ons mogelijk.</p>
  <p class="abs" style="left:388px;top:409px;width:185px;font-size:16px;line-height:28px;color:var(--white)">&nbsp;De producten worden (zo dicht mogelijk) bij de bron aangekocht of zelf ontwikkeld.</p>
  <p class="abs" style="left:650px;top:409px;width:170px;font-size:16px;line-height:28px;color:var(--white)">Door de directe lijnen zijn wij in staat tot snelle en flexibele levering tegen scherpe prijzen.</p>
  <p class="abs" style="left:912px;top:409px;width:185px;font-size:16px;line-height:28px;color:var(--white)">Hebben we een product niet in ons assortiment dan gaan we op zoek en vinden we een passende oplossing.</p>
</section>

<!-- Footer -->
<footer>
  <svg class="abs" style="left:0;top:3720px" width="1200" height="110" viewBox="0 0 1200 110">
    <path d="M0 92Q600 -20 1200 92V110H0Z" fill="#fff"/>
    <path d="M250 38Q600 8 940 38Q600 20 250 38Z" fill="#fff"/>
  </svg>
  <div class="abs brand" style="left:110px;top:3838px">
    <span class="brand-dot"></span><span class="brand-name">VAN ROOST</span>
  </div>
  <nav class="abs nav" style="left:688px;top:3848px">
    <a href="#">Huis</a>
    <a href="#" style="margin-left:38px">Over ons</a>
    <a href="#" style="margin-left:38px">Producten</a>
    <a href="#" style="margin-left:38px">Contact</a>
  </nav>
  <div class="abs" style="left:110px;top:3904px;width:979px;height:1px;background:#ddd"></div>

  <div class="abs" style="left:351px;top:3938px;width:1px;height:124px;background:#ddd"></div>
  <div class="abs" style="left:600px;top:3938px;width:1px;height:124px;background:#ddd"></div>
  <div class="abs" style="left:859px;top:3938px;width:1px;height:124px;background:#ddd"></div>

  <div class="abs" style="left:156px;top:3948px;font-size:15px;line-height:29px;color:#333">
    <div style="font-weight:700;font-size:14px;display:flex;align-items:center;gap:10px">
      <svg width="10" height="14" viewBox="0 0 10 14"><path d="M5 0A5 5 0 0 1 10 5C10 9 5 14 5 14S0 9 0 5A5 5 0 0 1 5 0Z" fill="var(--red)"/><circle cx="5" cy="5" r="2" fill="#fff"/></svg>ADRES</div>
    <div style="margin-top:3px">Lindenpad 12<br>6021 KM Hoorndal<br>Netherlands</div>
  </div>
  <div class="abs" style="left:413px;top:3948px;font-size:15px;line-height:29px;color:#333">
    <div style="font-weight:700;font-size:14px;display:flex;align-items:center;gap:10px">
      <svg width="13" height="13" viewBox="0 0 13 13"><path d="M2 0L5 3L3.5 5Q5 8 8 9.5L10 8L13 11L11 13Q6 13 3 10Q0 7 0 2Z" fill="var(--red)"/></svg>TELEFOON</div>
    <div style="margin-top:3px">+31 55 210 48 37</div>
  </div>
  <div class="abs" style="left:661px;top:3948px;font-size:15px;line-height:29px;color:#333">
    <div style="font-weight:700;font-size:14px;display:flex;align-items:center;gap:10px">
      <svg width="14" height="11" viewBox="0 0 14 11"><rect width="14" height="11" rx="1" fill="var(--red)"/><path d="M1 1L7 6L13 1" fill="none" stroke="#fff" stroke-width="1.3"/></svg>E-MAIL</div>
    <div style="margin-top:3px">sales@van-roost.nl</div>
  </div>
  <div class="abs" style="left:918px;top:3948px;font-size:15px;line-height:29px;color:#333">
    <div style="font-weight:700;font-size:14px">SOCIALE MEDIA</div>
    <div style="display:flex;gap:16px;margin-top:12px;margin-left:4px">
      <span style="width:26px;height:26px;border-radius:50%;background:var(--red)" aria-label="Social media link"></span>
      <span style="width:26px;height:26px;border-radius:50%;background:var(--red)" aria-label="Social media link"></span>
    </div>
  </div>

  <div class="abs" style="left:110px;top:4083px;width:979px;height:1px;background:#ddd"></div>
  <p class="abs" style="left:0;top:4104px;width:1200px;text-align:center;font-size:15px;color:#444">2022 Van Roost. Alle rechten voorbehouden.</p>
</footer>

</body>
</html>
```